Business card for my new company (Accounting firm)

I need a business card for my new business Brightwell Advisory and Ledger SA. Our services are accounting, tax, audit and financial management. Our customers are small companies, start-ups and new companies. The final design has to show financial security, trust and growth. Please find our logo attached to the business card. Text for the business card: Brightwell Advisory and Ledger SA Tomas Varenholt Director and Founder Certified Accountant Tel. 022 418 57 34 tv@clairevalconseil.ch www.clairevalconseil.ch Rue des Vergières 27 1201 Geneva
Target Market(s)
Our customers are small companies, start-ups and new companies.
Industry/Entity Type
Finance And Accounting
Contact Information for Business Card
Claireval Conseil et Comptes SA
Tomas Varenholt
Directeur et Fondateur
Expert-comptable diplômé
Tél. 022 418 57 34
tv@clairevalconseil.ch
www.clairevalconseil.ch
Rue des Vergières 27
1201 Genève

```html
<!DOCTYPE html>
<html lang="fr">
<head>
<meta charset="utf-8">
<title>Claireval Conseil et Comptes SA – Carte de visite</title>
<link rel="stylesheet" href="https://fonts.googleapis.com/css2?family=Montserrat:wght@500&family=Roboto:wght@400;500;700&display=swap">
<style>
  :root {
    --bg: #e4e5e7;
    --paper: #f7f7f7;
    --ink: #3a3b3d;
    --blue-dark: #1d6296;
    --blue-mid: #1f7db5;
    --blue-light: #2aa3d6;
    --white: #ffffff;
    --text-soft: #d7ebf7;
  }
  * { margin: 0; padding: 0; box-sizing: border-box; }
  html, body { width: 1200px; height: 726px; overflow: hidden; background: var(--bg); }
  body { position: relative; font-family: "Roboto", Arial, sans-serif; }

  .card {
    position: absolute;
    top: 214px;
    width: 520px;
    height: 298px;
    background: var(--paper);
    box-shadow: 0 6px 18px rgba(0,0,0,0.12);
    overflow: hidden;
  }
  .card--front { left: 50px; }
  .card--back { left: 630px; }

  /* Brand name block */
  .brand { display: flex; align-items: center; gap: 12px; color: var(--ink); font-family: "Montserrat", Arial, sans-serif; font-weight: 500; }
  .brand__mark { width: 16px; height: 16px; background: var(--blue-mid); flex: none; }
  .brand__text { display: flex; flex-direction: column; line-height: 1; }
  .brand__name { font-size: 40px; letter-spacing: 2px; text-transform: uppercase; }
  .brand__tagline { font-size: 11.5px; letter-spacing: 3.2px; text-transform: uppercase; margin-top: 6px; }

  .card--front .brand { position: absolute; left: 50%; top: 96px; transform: translateX(-50%); }
  .front__stripes { position: absolute; left: 0; top: 0; width: 520px; height: 298px; }

  /* Back */
  .back__band { position: absolute; left: 0; top: 0; width: 520px; height: 298px; }
  .card--back .brand { position: absolute; left: 26px; top: 64px; }
  .card--back .brand__name { font-size: 34px; }
  .card--back .brand__tagline { font-size: 10px; letter-spacing: 2.8px; }

  .person { position: absolute; left: 32px; top: 146px; color: var(--white); }
  .person__name { font-size: 19px; font-weight: 700; margin-bottom: 4px; }
  .person__role { font-size: 11.5px; color: var(--text-soft); line-height: 1.35; }

  .contact { position: absolute; left: 32px; top: 200px; list-style: none; color: var(--white); font-size: 12px; }
  .contact li { display: flex; align-items: center; gap: 9px; height: 17px; }
  .contact svg { width: 11px; height: 11px; fill: var(--white); flex: none; }

  .address { position: absolute; left: 32px; bottom: 14px; font-size: 13px; font-weight: 500; color: var(--ink); }
</style>
</head>
<body>

  <section class="card card--front" aria-label="Recto">
    <svg class="front__stripes" viewBox="0 0 520 298" aria-hidden="true">
      <polygon points="0,248 520,186 520,193 0,255" fill="var(--blue-light)"/>
      <polygon points="0,255 520,193 520,197 0,259" fill="var(--blue-dark)"/>
    </svg>
    <div class="brand">
      <span class="brand__mark"></span>
      <div class="brand__text">
        <span class="brand__name">Claireval</span>
        <span class="brand__tagline">Conseil et Comptes</span>
      </div>
    </div>
  </section>

  <section class="card card--back" aria-label="Verso">
    <svg class="back__band" viewBox="0 0 520 298" aria-hidden="true">
      <defs>
        <linearGradient id="bandFill" x1="0" y1="1" x2="1" y2="0">
          <stop offset="0" stop-color="var(--blue-dark)"/>
          <stop offset="1" stop-color="var(--blue-light)"/>
        </linearGradient>
      </defs>
      <polygon points="0,132 292,132 330,0 520,0 520,250 0,250" fill="url(#bandFill)"/>
    </svg>

    <div class="brand">
      <div class="brand__text">
        <span class="brand__name">Claireval</span>
        <span class="brand__tagline">Conseil et Comptes</span>
      </div>
    </div>

    <div class="person">
      <p class="person__name">Tomas Varenholt</p>
      <p class="person__role">Directeur et Fondateur<br>Expert-comptable diplômé</p>
    </div>

    <ul class="contact">
      <li>
        <svg viewBox="0 0 24 24" aria-hidden="true"><path d="M6.6 10.8a15 15 0 0 0 6.6 6.6l2.2-2.2c.3-.3.7-.4 1-.2 1.1.4 2.3.6 3.6.6.6 0 1 .4 1 1V20c0 .6-.4 1-1 1A17 17 0 0 1 3 4c0-.6.4-1 1-1h3.5c.6 0 1 .4 1 1 0 1.3.2 2.5.6 3.6.1.3 0 .7-.2 1z"/></svg>
        <span>022 418 57 34</span>
      </li>
      <li>
        <svg viewBox="0 0 24 24" aria-hidden="true"><path d="M2 5h20v14H2zm2 2v.5l8 5 8-5V7l-8 5z"/></svg>
        <span>tv@clairevalconseil.ch</span>
      </li>
      <li>
        <svg viewBox="0 0 24 24" aria-hidden="true"><path d="M12 2a10 10 0 1 0 0 20 10 10 0 0 0 0-20zm6.9 9h-3a15 15 0 0 0-1.2-5.4A8 8 0 0 1 18.9 11zM12 4c.9 1.2 1.7 3.7 1.9 7h-3.8c.2-3.3 1-5.8 1.9-7zM9.3 5.6A15 15 0 0 0 8.1 11h-3a8 8 0 0 1 4.2-5.4zM5.1 13h3a15 15 0 0 0 1.2 5.4A8 8 0 0 1 5.1 13zm6.9 7c-.9-1.2-1.7-3.7-1.9-7h3.8c-.2 3.3-1 5.8-1.9 7zm2.7-1.6a15 15 0 0 0 1.2-5.4h3a8 8 0 0 1-4.2 5.4z"/></svg>
        <span>www.clairevalconseil.ch</span>
      </li>
    </ul>

    <p class="address">Rue des Vergières 27 1201 Genève</p>
  </section>

</body>
</html>
```